Business Card Design Project

We need a Business Card for an Mechanical Engineering firm in Singapore. The design should be Modern & Technical looking, yet eye catching.

Our company deals in Cutting Tools & Machine Accessories for the Manufacturing Industries such as Oil & Gas, Aero Space, etc... For more information on our Company, you can either email me or view our website www.torvalen.com.sg.

We are trying to revamp our image to give our consumers a fresh new perspective to our company, so we welcome all ideas.

Industry/Entity Type

Business

Requirements
Must have
• Must incorporate New Company Logo into the card as shown in Uploaded file.

```html
<!DOCTYPE html>
<html lang="en">
<head>
<meta charset="utf-8">
<title>Torvalen Tools – Business Card</title>
<link rel="stylesheet" href="https://fonts.googleapis.com/css2?family=Open+Sans:ital,wght@0,400;0,600;0,700;1,400&display=swap">
<style>
  :root {
    --brand-red: #8b1c24;
    --brand-red-dark: #6e141b;
    --ink: #2b2b2b;
    --card: #ffffff;
    --backdrop: #e6e6e6;
    --wave-grey: #d9d9d9;
    --wave-line: #1e1e1e;
  }
  * { box-sizing: border-box; margin: 0; padding: 0; }
  html, body { width: 1200px; height: 944px; overflow: hidden; }
  body {
    background: var(--backdrop);
    font-family: "Open Sans", Arial, sans-serif;
    color: var(--ink);
    position: relative;
  }
  .card {
    position: absolute;
    width: 620px;
    height: 370px;
    background: var(--card);
    border-radius: 22px;
    overflow: hidden;
    box-shadow: 0 6px 18px rgba(0,0,0,0.18);
  }
  .card--front { left: 60px; top: 60px; }
  .card--back { left: 520px; top: 514px; }

  .wordmark { display: flex; align-items: center; gap: 12px; }
  .wordmark__dot { width: 22px; height: 22px; border-radius: 50%; background: var(--brand-red); flex: none; }
  .wordmark__name {
    font-weight: 700;
    color: var(--brand-red);
    text-transform: uppercase;
    letter-spacing: 1px;
    white-space: nowrap;
  }

  .card--front .wordmark { position: absolute; left: 0; right: 0; top: 128px; justify-content: center; }
  .card--front .wordmark__name { font-size: 44px; }
  .front-url {
    position: absolute; left: 0; right: 0; top: 236px;
    text-align: center; font-size: 19px; letter-spacing: 0.5px; color: var(--ink);
  }

  .card--back .wordmark { position: absolute; left: 50px; top: 84px; }
  .card--back .wordmark__dot { width: 18px; height: 18px; }
  .card--back .wordmark__name { font-size: 28px; }

  .person { position: absolute; left: 408px; top: 92px; }
  .person__name { font-size: 20px; font-weight: 600; color: var(--ink); line-height: 24px; }
  .person__role { font-size: 15px; font-style: italic; color: var(--brand-red); line-height: 20px; }

  .address {
    position: absolute; left: 50px; top: 200px;
    display: flex; gap: 8px;
    font-size: 17px; line-height: 24px; color: var(--ink);
  }
  .contacts {
    position: absolute; left: 388px; top: 198px;
    list-style: none;
    font-size: 17px; line-height: 22px; color: var(--ink);
  }
  .contacts li { display: flex; align-items: center; gap: 8px; white-space: nowrap; }
  .contacts .accent { color: var(--brand-red); }
  .icon { width: 14px; height: 14px; flex: none; fill: var(--brand-red); }
  .address .icon { margin-top: 5px; }

  .card__wave { position: absolute; left: 0; top: 220px; width: 620px; height: 150px; }
</style>
</head>
<body>

<section class="card card--front" aria-label="Card front">
  <div class="wordmark">
    <span class="wordmark__dot"></span>
    <span class="wordmark__name">Torvalen Tools</span>
  </div>
  <p class="front-url">www.torvalentools.com</p>
</section>

<section class="card card--back" aria-label="Card back">
  <svg class="card__wave" viewBox="0 0 620 150" preserveAspectRatio="none" aria-hidden="true">
    <path d="M0 38 C180 70 380 82 620 92 L620 150 L0 150 Z" fill="var(--wave-grey)"/>
    <path d="M0 46 C180 80 380 92 620 102" fill="none" stroke="var(--wave-line)" stroke-width="5"/>
    <path d="M0 54 C180 90 380 100 620 110 L620 150 L0 150 Z" fill="var(--brand-red)"/>
    <path d="M0 112 C200 138 420 118 620 128 L620 150 L0 150 Z" fill="var(--brand-red-dark)" opacity="0.6"/>
  </svg>

  <div class="wordmark">
    <span class="wordmark__dot"></span>
    <span class="wordmark__name">Torvalen Tools</span>
  </div>

  <div class="person">
    <p class="person__name">Marcus Hale</p>
    <p class="person__role">manager</p>
  </div>

  <div class="address">
    <svg class="icon" viewBox="0 0 14 14" aria-hidden="true"><path d="M7 1 L14 7 H12 V13 H8.5 V9 H5.5 V13 H2 V7 H0 Z"/></svg>
    <p>1450 Kellan Ridge Rd.<br>Ashford, TX 78114</p>
  </div>

  <ul class="contacts">
    <li><svg class="icon" viewBox="0 0 14 14" aria-hidden="true"><path d="M3 1 L5.5 1 L6.5 4.5 L5 5.8 C5.8 7.6 6.6 8.4 8.2 9 L9.5 7.5 L13 8.5 L13 11 C13 12.2 12 13 10.8 13 C5.5 12.5 1.5 8.5 1 3.2 C1 2 1.8 1 3 1 Z"/></svg>512-555-0140</li>
    <li><svg class="icon" viewBox="0 0 14 14" aria-hidden="true"><path d="M4 0.5 H10 A1 1 0 0 1 11 1.5 V12.5 A1 1 0 0 1 10 13.5 H4 A1 1 0 0 1 3 12.5 V1.5 A1 1 0 0 1 4 0.5 Z M4.5 2 V10.5 H9.5 V2 Z"/></svg>512-555-0141</li>
    <li><svg class="icon" viewBox="0 0 14 14" aria-hidden="true"><path d="M1 3 H13 V11 H1 Z"/></svg>info@torvalentools.com</li>
    <li><svg class="icon" viewBox="0 0 14 14" aria-hidden="true"><circle cx="7" cy="7" r="6"/></svg><span>www.<span class="accent">torvalentools</span>.com</span></li>
  </ul>
</section>

</body>
</html>
```